FunBrixo Business Card

We need a business card design for our company. We sell construction-themed amusement rides for kids.

Contact Information for Business Card

Contact info on business card should include:
Carl Dunning
Co-Founder & COO
(833) 571-FUNBRIX
Carl@funbrixo-demo.com
www.funbrixo-demo.com

```html
<!DOCTYPE html>
<html lang="en">
<head>
<meta charset="utf-8">
<title>FunBrixo Business Card</title>
<link href="https://fonts.googleapis.com/css2?family=Poppins:wght@400;500;700;800&display=swap" rel="stylesheet">
<style>
  :root {
    --backdrop: #d9d9db;
    --paper: #ffffff;
    --orange: #f07a22;
    --amber: #f5a11c;
    --purple: #8e2b93;
    --sky: #1fa6e0;
    --magenta: #e2187f;
    --ink: #3a3a3a;
    --photo-light: #e6e6e6;
    --photo-mid: #a9a9a9;
    --photo-dark: #5e5e5e;
  }
  * { box-sizing: border-box; margin: 0; padding: 0; }
  html, body { width: 1200px; height: 801px; overflow: hidden; }
  body {
    background: var(--backdrop);
    font-family: "Poppins", sans-serif;
    display: flex;
    align-items: center;
    justify-content: center;
    gap: 40px;
  }
  .card {
    position: relative;
    width: 560px;
    height: 320px;
    background: var(--paper);
    overflow: hidden;
    box-shadow: 0 6px 18px rgba(0,0,0,.15);
  }
  .edge-band {
    position: absolute;
    left: 0; right: 0;
    height: 10px;
    display: flex;
  }
  .edge-band.top { top: 0; }
  .edge-band.bottom { bottom: 0; }
  .edge-band span { flex: 1; }
  .seg-orange { background: var(--orange); }
  .seg-purple { background: var(--purple); }
  .seg-sky { background: var(--sky); }
  .seg-magenta { background: var(--magenta); }
  .seg-amber { background: var(--amber); }

  /* front */
  .front-layout {
    position: absolute;
    inset: 10px 0;
    display: flex;
    align-items: center;
  }
  .brand-block {
    width: 270px;
    display: flex;
    align-items: center;
    justify-content: center;
    gap: 10px;
  }
  .brand-dot {
    width: 22px; height: 22px;
    border-radius: 50%;
    background: var(--purple);
  }
  .brand-name {
    font-weight: 800;
    font-size: 38px;
    color: var(--orange);
    letter-spacing: -0.5px;
  }
  .divider {
    width: 1px;
    height: 110px;
    background: var(--orange);
  }
  .contact-block {
    padding-left: 28px;
  }
  .person-name {
    font-weight: 700;
    font-size: 20px;
    color: var(--orange);
    text-transform: uppercase;
    line-height: 1.1;
  }
  .person-title {
    font-size: 14px;
    color: var(--sky);
    margin-bottom: 12px;
  }
  .contact-line {
    display: flex;
    align-items: center;
    gap: 8px;
    font-size: 13px;
    color: var(--ink);
    line-height: 1.6;
  }
  .contact-line svg { width: 12px; height: 12px; flex: none; }

  /* back */
  .photo-fill {
    position: absolute;
    inset: 10px 0;
    background: linear-gradient(170deg, var(--photo-light) 0%, var(--photo-mid) 55%, var(--photo-dark) 100%);
  }
  .back-brand {
    position: absolute;
    left: 50%; top: 50%;
    transform: translate(-50%, -50%);
    display: flex;
    align-items: center;
    gap: 12px;
  }
  .back-brand .brand-name { font-size: 54px; }
  .back-brand .brand-dot { width: 30px; height: 30px; }
</style>
</head>
<body>

  <section class="card card-front">
    <div class="edge-band top">
      <span class="seg-orange"></span><span class="seg-purple"></span><span class="seg-sky"></span><span class="seg-magenta"></span><span class="seg-amber"></span>
    </div>
    <div class="front-layout">
      <div class="brand-block">
        <span class="brand-name">FunBrixo</span>
        <span class="brand-dot"></span>
      </div>
      <div class="divider"></div>
      <div class="contact-block">
        <p class="person-name">Carl Dunning</p>
        <p class="person-title">Co-Founder &amp; COO</p>
        <p class="contact-line">
          <svg viewBox="0 0 12 12"><path d="M2.5 1h2l1 3-1.5 1a6 6 0 0 0 3 3l1-1.5 3 1v2a1 1 0 0 1-1 1A10 10 0 0 1 1.5 2a1 1 0 0 1 1-1z" fill="var(--orange)"/></svg>
          (833) 571-FUNBRIX
        </p>
        <p class="contact-line">
          <svg viewBox="0 0 12 12"><rect x="0.5" y="2" width="11" height="8" rx="1" fill="var(--orange)"/><path d="M1 3l5 4 5-4" stroke="#fff" fill="none"/></svg>
          Carl@funbrixo-demo.com
        </p>
        <p class="contact-line">
          <svg viewBox="0 0 12 12"><circle cx="6" cy="6" r="5.5" fill="var(--orange)"/><path d="M1 6h10M6 1c2 2 2 8 0 10M6 1c-2 2-2 8 0 10" stroke="#fff" fill="none" stroke-width=".8"/></svg>
          www.funbrixo-demo.com
        </p>
      </div>
    </div>
    <div class="edge-band bottom">
      <span class="seg-orange"></span><span class="seg-purple"></span><span class="seg-sky"></span><span class="seg-magenta"></span><span class="seg-amber"></span>
    </div>
  </section>

  <section class="card card-back">
    <div class="edge-band top">
      <span class="seg-sky"></span><span class="seg-magenta"></span><span class="seg-amber"></span><span class="seg-orange"></span><span class="seg-purple"></span>
    </div>
    <div class="photo-fill" role="img" aria-label="Black and white photo of a kids construction-themed amusement park with mini excavators, fences and a wheelbarrow"></div>
    <div class="back-brand">
      <span class="brand-name">FunBrixo</span>
      <span class="brand-dot"></span>
    </div>
    <div class="edge-band bottom">
      <span class="seg-orange"></span><span class="seg-purple"></span><span class="seg-sky"></span><span class="seg-magenta"></span><span class="seg-amber"></span>
    </div>
  </section>

</body>
</html>
```